Larkspur Talent IT Recruiting firm needs a business card design for Recruiters, Sourcers, and Account

We need business cards that allow us to change all contact info, names, titles (Recruiter, Sourcer, Account Manager, Director, CEO, etc) per person since we have three offices, in three cities, Phoenix, Austin, and Las Vegas. We do recruiting and contractors for IT positions (Developers, Architects, Software Engineers, Security Engineers, Help Desk, DBAs, PMs, Scrum Masters, etc.) Our client companies are very diverse from Meridian 100 to silicone Valley type start-ups.

So, while we what hip, techie, and quirky, it still needs to be professional. Primary color we use is blue, with silver as a secondary color.

Target Market(s)

IT, Technology

Industry/Entity Type

Business

Contact Information for Business Card

Company name: Larkspur Talent, Inc.
Website: www.larkspurtalent.example
Logos for Careerloop, Blipster, and Myriada

Name, Title, Office Number, Cell Number, email

Font styles to use
Serif
Sans Serif

Colors
0455a3
d5d5d5

Requirements
Nice to have
• The grey I selected below is not necessary - but, would like silver included. I included a card design (File 3: LTI early trial example.jpg) that I had started on. It's very rough, and not quite what we're looking for, but what we did like is the logo, big, maybe a bit faded, off center, goes out of frame, etc. Still looking for other ideas - you are the pros! But, just an idea of a design element we liked.

```html
<!DOCTYPE html>
<html lang="en">
<head>
<meta charset="utf-8">
<title>Larkspur Talent business card</title>
<link rel="stylesheet" href="https://fonts.googleapis.com/css2?family=Cinzel:wght@400&family=Oswald:wght@400;500&family=Roboto:wght@300;400&display=swap">
<style>
  :root {
    --page: #e9e9ea;
    --card: #ffffff;
    --blue: #0a74c4;
    --blue-deep: #0455a3;
    --blue-mid: #0a68b4;
    --blue-light: #1a86d6;
    --silver: #d5d5d5;
    --ink: #3a3a3c;
    --white: #ffffff;
  }
  * { box-sizing: border-box; margin: 0; padding: 0; }
  html, body { width: 1200px; height: 970px; overflow: hidden; }
  body {
    background: var(--page);
    display: flex;
    flex-direction: column;
    align-items: center;
    justify-content: center;
    gap: 30px;
  }
  .card {
    width: 770px;
    height: 440px;
    background: var(--card);
    box-shadow: 0 6px 18px rgba(0,0,0,0.18);
    position: relative;
    overflow: hidden;
  }
  /* back of card */
  .card-back {
    display: flex;
    align-items: center;
    justify-content: center;
    gap: 22px;
    background: linear-gradient(160deg, #ffffff 0%, #f1f1f2 60%, var(--silver) 100%);
  }
  .brand-dot {
    width: 54px; height: 54px; border-radius: 50%;
    background: var(--blue);
  }
  .brand-name {
    font-family: "Cinzel", serif;
    font-weight: 400;
    font-size: 44px;
    letter-spacing: 3px;
    color: var(--blue-deep);
  }
  /* front of card */
  .card-front { display: flex; }
  .front-brand {
    width: 45%;
    display: flex;
    flex-direction: column;
    align-items: center;
    justify-content: center;
    gap: 12px;
    background: linear-gradient(160deg, #ffffff 0%, #f2f2f3 100%);
  }
  .front-brand .wordmark {
    font-family: "Cinzel", serif;
    font-weight: 400;
    font-size: 30px;
    letter-spacing: 3px;
    color: var(--ink);
  }
  .front-brand .tagline {
    font-family: "Cinzel", serif;
    font-size: 12px;
    letter-spacing: 2px;
    color: var(--ink);
  }
  .front-info {
    width: 55%;
    position: relative;
    color: var(--white);
    background: linear-gradient(90deg,
      var(--blue-mid) 0%, var(--blue-mid) 18%,
      var(--blue-deep) 18%, var(--blue-deep) 38%,
      var(--blue) 38%, var(--blue) 64%,
      var(--blue-light) 64%, var(--blue-light) 100%);
    padding: 40px 34px;
    display: flex;
    flex-direction: column;
    justify-content: space-between;
  }
  .address {
    font-family: "Roboto", sans-serif;
    font-weight: 300;
    font-size: 15px;
    line-height: 1.5;
  }
  .person { text-align: right; }
  .person .name {
    font-family: "Oswald", sans-serif;
    font-weight: 500;
    font-size: 28px;
    letter-spacing: 1px;
  }
  .person .title {
    font-family: "Roboto", sans-serif;
    font-size: 13px;
    letter-spacing: 2px;
  }
  .contacts {
    list-style: none;
    font-family: "Roboto", sans-serif;
    font-weight: 300;
    font-size: 12px;
    text-align: right;
    line-height: 1.9;
  }
  .contacts li { display: flex; justify-content: flex-end; align-items: center; gap: 8px; }
  .contacts svg { width: 11px; height: 11px; fill: var(--white); }
</style>
</head>
<body>
  <section class="card card-back">
    <span class="brand-dot"></span>
    <span class="brand-name">Larkspur Talent</span>
  </section>

  <section class="card card-front">
    <div class="front-brand">
      <span class="wordmark">LARKSPUR TALENT</span>
      <span class="tagline">BUILT FOR THE NEXT HIRE</span>
    </div>
    <div class="front-info">
      <p class="address">42 Meadow Road<br>Suite 7, Harbor Lane</p>
      <div class="person">
        <p class="name">DANA WHITFIELD</p>
        <p class="title">GENERAL MANAGER</p>
      </div>
      <ul class="contacts">
        <li>555 014 2277
          <svg viewBox="0 0 24 24"><path d="M6.6 10.8a15 15 0 0 0 6.6 6.6l2.2-2.2a1 1 0 0 1 1-.25 11 11 0 0 0 3.6.6 1 1 0 0 1 1 1V20a1 1 0 0 1-1 1A17 17 0 0 1 3 4a1 1 0 0 1 1-1h3.5a1 1 0 0 1 1 1 11 11 0 0 0 .6 3.6 1 1 0 0 1-.25 1z"/></svg></li>
        <li>555 014 3390
          <svg viewBox="0 0 24 24"><rect x="6" y="2" width="12" height="20" rx="2"/></svg></li>
        <li>dana@larkspurtalent.example
          <svg viewBox="0 0 24 24"><path d="M2 5h20v14H2z"/></svg></li>
        <li>www.larkspurtalent.example
          <svg viewBox="0 0 24 24"><circle cx="12" cy="12" r="10"/></svg></li>
      </ul>
    </div>
  </section>
</body>
</html>
```